Bramwell Lodge Business Cards design with a logo

I want two Business cards designed with a very modern contemporary logo UNING 1920'S FONT STYLES with the following details

Address:
Bramwell Lodge
17 Pellham Road
Helensburgh
G83 2RN

Details for card 1

Name: Dermot Ashby
email: Dermot.ashby@bramwell.lodge
Tel : +971 52 318 6094
Tel +44 7700 900 318

Details Card 2

Name: Dermot Ashby
email: Neville.osgood@bramwell.lodge
Tel : +971 52 430 9187

Bramwell lodge is a house that was built around 1880 and was used extensively in the 1920's for entertaining and parties in the arts scene, the house again will be resurrected to a modern entertainment venue

If you have any questions feel free to ask

Target Market(s)

The market for this is the young modern crowd

Industry/Entity Type

Entertainment Industry

Contact Information for Business Card

Address:
Bramwell Lodge
17 Pellham Road
Helensburgh
G83 2RN

Details for card 1

Name: Dermot Ashby
Tel : +971 52 318 6094
Tel +44 7700 900 318

Details Card 2

Name: Neville Osgood
Tel : +971 52 430 9187

Logo Text

Bramwell Lodge

Font styles to use
Other font styles liked:
• 1920'S FONT STULES

Requirements
Must have
• Modern Contemporary, whilst taking into consideration the age of the house as detailed above. YOU MUT BE USING 1920'S FONT STYLES
Nice to have
• 1920'S FONT STYLES see attached image if a suggestion
Should not have
• Should not look old or dated

```html
<!DOCTYPE html>
<html lang="en">
<head>
<meta charset="utf-8">
<title>Bramwell Lodge Business Cards</title>
<link href="https://fonts.googleapis.com/css2?family=Federo&display=swap" rel="stylesheet">
<style>
  :root {
    --backdrop: #1c1c1d;
    --card-dark: #141414;
    --card-mid: #262626;
    --ink: #f4f4f4;
    --rule: #bdbdbd;
  }
  * { margin: 0; padding: 0; box-sizing: border-box; }
  html, body {
    width: 1200px;
    height: 900px;
    overflow: hidden;
    background: var(--backdrop);
    font-family: "Federo", sans-serif;
    color: var(--ink);
  }
  .sheet {
    position: relative;
    width: 1200px;
    height: 900px;
  }
  .card {
    position: absolute;
    left: 250px;
    width: 700px;
    height: 400px;
    overflow: hidden;
    background: var(--card-dark);
  }
  .card--front { top: 40px; }
  .card--back { top: 460px; }
  .card__pattern {
    position: absolute;
    inset: 0;
    background:
      radial-gradient(ellipse at 60% 40%, rgba(70,70,70,0.55), rgba(20,20,20,0) 70%),
      linear-gradient(135deg, var(--card-mid), var(--card-dark));
  }
  .card__content { position: absolute; inset: 0; }

  .brand-name {
    position: absolute;
    top: 130px;
    left: 0;
    right: 0;
    text-align: center;
    font-size: 66px;
    letter-spacing: 1px;
    color: var(--ink);
  }
  .brand-web {
    position: absolute;
    bottom: 44px;
    left: 0;
    right: 0;
    text-align: center;
    font-size: 15px;
    letter-spacing: 1.5px;
    text-transform: uppercase;
  }

  .person {
    position: absolute;
    top: 150px;
    left: 40px;
    width: 260px;
    text-align: right;
    text-transform: uppercase;
  }
  .person__name { font-size: 30px; letter-spacing: 1px; line-height: 1; }
  .person__role { font-size: 13px; letter-spacing: 1.5px; margin-top: 8px; }
  .divider {
    position: absolute;
    top: 140px;
    left: 325px;
    width: 1px;
    height: 90px;
    background: var(--rule);
  }
  .contacts {
    position: absolute;
    top: 145px;
    left: 345px;
    list-style: none;
    text-transform: uppercase;
    font-size: 16px;
    letter-spacing: 1px;
  }
  .contacts li {
    display: flex;
    align-items: center;
    gap: 12px;
    height: 21px;
  }
  .contacts svg { width: 12px; height: 12px; flex: none; }
  .address {
    position: absolute;
    left: 40px;
    bottom: 54px;
    display: flex;
    align-items: center;
    gap: 14px;
    font-size: 15px;
    letter-spacing: 1.3px;
    text-transform: uppercase;
  }
  .address__mark {
    width: 18px;
    height: 18px;
    background: var(--ink);
  }
</style>
</head>
<body>
<main class="sheet">
  <section class="card card--front">
    <div class="card__pattern" role="img" aria-label="Art deco pattern of nested diamonds, dotted lines and fan rays in soft grey on black"></div>
    <div class="card__content">
      <h1 class="brand-name">Bramwell Lodge</h1>
      <p class="brand-web">www.bramwelllodge.com</p>
    </div>
  </section>

  <section class="card card--back">
    <div class="card__pattern" role="img" aria-label="Art deco pattern of nested diamonds, dotted lines and fan rays in soft grey on black"></div>
    <div class="card__content">
      <div class="person">
        <h2 class="person__name">Dermot Ashby</h2>
        <p class="person__role">Director</p>
      </div>
      <div class="divider"></div>
      <ul class="contacts">
        <li>
          <svg viewBox="0 0 12 12" aria-hidden="true"><path d="M2.5 1 L4.5 1 L5 3.5 L3.8 4.3 Q4.8 6.8 7.7 8.2 L8.5 7 L11 7.5 L11 9.5 Q10.5 11 9 11 Q1 9.5 1 2.5 Q1 1 2.5 1 Z" fill="#f4f4f4"/></svg>
          <span>+971 52 318 6094</span>
        </li>
        <li>
          <svg viewBox="0 0 12 12" aria-hidden="true"><path d="M1 4 Q6 0.5 11 4 L10 5.5 L8 5 L8 4 Q6 3.2 4 4 L4 5 L2 5.5 Z" fill="#f4f4f4"/><rect x="2.5" y="6.5" width="7" height="4.5" rx="0.8" fill="#f4f4f4"/></svg>
          <span>+44 7700 900 318</span>
        </li>
        <li>
          <svg viewBox="0 0 12 12" aria-hidden="true"><rect x="1" y="2.5" width="10" height="7" fill="none" stroke="#f4f4f4" stroke-width="1"/><path d="M1 2.5 L6 6.5 L11 2.5" fill="none" stroke="#f4f4f4" stroke-width="1"/></svg>
          <span>Dermot.ashby@bramwell.lodge</span>
        </li>
        <li>
          <svg viewBox="0 0 12 12" aria-hidden="true"><circle cx="6" cy="6" r="5" fill="none" stroke="#f4f4f4" stroke-width="1"/><ellipse cx="6" cy="6" rx="2.2" ry="5" fill="none" stroke="#f4f4f4" stroke-width="0.9"/><path d="M1 6 H11" stroke="#f4f4f4" stroke-width="0.9"/></svg>
          <span>www.bramwelllodge.com</span>
        </li>
      </ul>
      <p class="address">
        <span class="address__mark"></span>
        <span>Bramwell Lodge, 17 Pellham Road Helensburgh&nbsp;&nbsp;G83 2RN</span>
      </p>
    </div>
  </section>
</main>
</body>
</html>
```